We need a package design for a dietary supplement.

We need a package design for a dietary supplement - throwable tablets - Senegalese acacia fiber with pineapple flavor.
New name BrightOrbit.
Remember the packaging is a white jar, a magenta cap, a sticker, and a cardboard box. We want to change the name to: BrightOrbit (if you have a better idea for the name, just tell me) and refresh the packaging.
Product description:
> Contributes to improving the functioning of the digestive system.
> Boosts metabolism, controls appetite and supports weight loss.
> Helps maintain normal blood sugar levels.
> Regulates cholesterol levels
> 100% natural ingredients in the form of chewable tablets.
It has many beneficial health benefits:
> Cleanses the body of toxins,
> Helps with constipation and bloating,
> Facilitates defecation,
> Regulates cholesterol levels (by eliminating bile acids from the intestine),
> Adds energy,
> Improves metabolism,
> reduces appetite,
> Improves the work of the digestive system,
> It can help to get rid of the unpleasant smell from the mouth,
> Improves well-being,
> Regular intake can lead to weight loss,
> It works gently and does not cause side effects,
> Delays the aging process,
> Improves the appearance of the skin
This all-natural dietary supplement supports heart health, helps maintain blood sugar levels, soothes irritable bowel syndrome, and improves overall gut health.

100% natural, vegan product, no added sugars, no added salt. It has only 2 ingredients: Cenegal acacia and pineapple juice.

We are changing the name and packaging for our product called KestroNuma. Photos attached, packaging grid attached, samples of our other packaging attached.
*Packaging in Dutch

Target Market(s)

Netherlands

Industry/Entity Type

dietary supplements

Colors

Designer to choose colors to be used in the design.

Requirements
Must have
• Modern and inspire patient confidence.
Nice to have
• Good, natural, healthy
Should not have
• It should not clearly indicate that it has a slimming effect, as in the kestronuma project

```html
<!DOCTYPE html>
<html lang="en">
<head>
<meta charset="utf-8">
<title>BrightOrbit – Senegalese Acacia Fiber label</title>
<link href="https://fonts.googleapis.com/css2?family=Antonio:wght@600&family=Poppins:wght@300;400;700&family=Barlow+Condensed:ital,wght@1,600&display=swap" rel="stylesheet">
<style>
  :root {
    --navy: #13234d;
    --magenta: #b3166f;
    --magenta-deep: #c0127c;
    --magenta-light: #e6b3d2;
    --blue-dark: #3f5a80;
    --blue-light: #c9d1dd;
    --green: #3ea664;
    --page: #f3f3f4;
    --label: #ffffff;
    --ink: #222633;
  }
  * { margin: 0; padding: 0; box-sizing: border-box; }
  html, body { width: 1200px; height: 1200px; overflow: hidden; background: var(--page); }
  .label {
    position: absolute; left: 98px; top: 45px;
    width: 1005px; height: 1110px;
    background: var(--label);
    overflow: hidden;
    font-family: "Poppins", sans-serif;
  }
  .bands { position: absolute; inset: 0; }
  .brand {
    position: absolute; top: 190px; left: 0; width: 960px;
    display: flex; justify-content: center; align-items: center; gap: 14px;
  }
  .brand-dot { width: 22px; height: 22px; border-radius: 50%; background: var(--magenta); }
  .brand-name {
    font-family: "Poppins", sans-serif; font-weight: 700;
    font-size: 46px; letter-spacing: 0.02em; color: var(--navy);
  }
  .count {
    position: absolute; top: 48px; left: 780px; width: 150px;
    text-align: center; color: var(--navy);
  }
  .count-number { font-weight: 300; font-size: 84px; line-height: 1; letter-spacing: -0.03em; }
  .count-unit { font-weight: 400; font-size: 19px; line-height: 1.4; margin-top: 8px; }
  .product-name { position: absolute; top: 290px; left: 80px; width: 800px; height: 200px; }
  .product-name text { font-family: "Antonio", sans-serif; font-weight: 600; font-size: 238px; }
  .product-name .part-a { fill: var(--navy); }
  .product-name .part-b { fill: var(--magenta); }
  .ingredient {
    position: absolute; top: 490px; left: 0; width: 960px; text-align: center;
    font-weight: 300; font-size: 40px; letter-spacing: 0.17em; color: var(--ink);
  }
  .product-visual {
    position: absolute; left: 225px; top: 560px; width: 440px; height: 350px;
    border-radius: 40% 45% 42% 38%;
    background: radial-gradient(circle at 65% 75%, #6b3a1c 0 22%, transparent 23%),
                linear-gradient(135deg, #f7e07a 0%, #f1c232 55%, #d79a1e 100%);
  }
  .vegan-tag {
    position: absolute; left: 192px; top: 594px; width: 305px; height: 40px;
    background: linear-gradient(90deg, var(--green) 70%, rgba(62,166,100,0.2));
    color: #fff; font-size: 21px; font-weight: 400;
    display: flex; align-items: center; gap: 10px; padding-left: 18px;
  }
  .vegan-tag svg { width: 24px; height: 24px; }
  .claims {
    position: absolute; left: 118px; top: 935px; list-style: none;
    font-family: "Barlow Condensed", sans-serif; font-style: italic; font-weight: 600;
    font-size: 40px; color: var(--navy);
  }
  .claims li { display: flex; align-items: center; gap: 12px; line-height: 50px; }
  .claims li:first-child { margin-left: 14px; }
  .claims svg { width: 28px; height: 28px; }
</style>
</head>
<body>
  <section class="label">
    <svg class="bands" viewBox="0 0 1005 1110" width="1005" height="1110" aria-hidden="true">
      <defs>
        <linearGradient id="band-blue" x1="0" y1="0" x2="0" y2="1">
          <stop offset="0" stop-color="var(--blue-dark)"/>
          <stop offset="1" stop-color="var(--blue-light)"/>
        </linearGradient>
        <linearGradient id="band-magenta" x1="0" y1="0" x2="0" y2="1">
          <stop offset="0" stop-color="var(--magenta-light)"/>
          <stop offset="0.55" stop-color="#d457a4"/>
          <stop offset="1" stop-color="var(--magenta-deep)"/>
        </linearGradient>
      </defs>
      <path d="M0 0 L165 0 C150 120 100 250 90 380 C80 500 190 600 180 800 C175 950 150 1050 120 1110 L0 1110 Z" fill="url(#band-blue)"/>
      <path d="M1005 40 C960 120 920 250 900 330 C870 450 840 560 838 700 L842 1110 L1005 1110 Z" fill="url(#band-magenta)"/>
    </svg>

    <div class="count">
      <div class="count-number">100</div>
      <div class="count-unit">THROWABLE<br>TABLETS</div>
    </div>

    <div class="brand">
      <span class="brand-dot"></span>
      <span class="brand-name">CENDRA FARMA</span>
    </div>

    <svg class="product-name" viewBox="0 0 800 200" width="800" height="200">
      <text x="0" y="190" textLength="800" lengthAdjust="spacingAndGlyphs"><tspan class="part-a">BRIGHT</tspan><tspan class="part-b">ORBIT</tspan></text>
    </svg>

    <div class="ingredient">SENEGALESE ACACIA FIBER</div>

    <div class="product-visual" role="img" aria-label="Pineapple wedges with a small wooden bowl of acacia gum pieces"></div>

    <div class="vegan-tag">
      <svg viewBox="0 0 24 24" aria-hidden="true"><path d="M4 20 C6 12 12 7 20 5 C19 13 14 18 6 19 Z" fill="#fff"/></svg>
      VEGAN PRODUCT
    </div>

    <ul class="claims">
      <li><svg viewBox="0 0 24 24" aria-hidden="true"><path d="M3 13 L9 19 L21 4" fill="none" stroke="var(--magenta)" stroke-width="4" stroke-linecap="round"/></svg>REGULATES CHOLESTEROL LEVELS</li>
      <li><svg viewBox="0 0 24 24" aria-hidden="true"><path d="M3 13 L9 19 L21 4" fill="none" stroke="var(--magenta)" stroke-width="4" stroke-linecap="round"/></svg>BOOSTS METABOLISM</li>
    </ul>
  </section>
</body>
</html>
```